Medical Clinic Group Looking for Website Design

We own and operate medical clinics and are looking looking to revamp our website. Our current website is www.brightpathcareclinics.ca We need our website to be more functional, user friendly, and easier to maintain.

```html
<!DOCTYPE html>
<html lang="en">
<head>
<meta charset="utf-8">
<title>BrightPath Care Clinics</title>
<link href="https://fonts.googleapis.com/css2?family=Jost:wght@400;500;600;700&family=Mulish:wght@400;500&display=swap" rel="stylesheet">
<style>
:root{
  --teal:#33d3de;
  --teal-dark:#1fb2bd;
  --teal-soft:#e6f8fa;
  --ink:#1a1a1a;
  --body:#333;
  --frame:#77787a;
  --faint:#f0f0f2;
  --foot-bg:#f5f5f7;
  --line:#d4d4d8;
}
*{margin:0;padding:0;box-sizing:border-box}
html,body{width:713px;height:1200px;overflow:hidden;background:#fff}
body{position:relative;font-family:"Mulish",sans-serif;color:var(--body)}
.abs{position:absolute}
.head-font{font-family:"Jost",sans-serif}

/* header */
.site-header{position:absolute;left:0;top:0;width:713px;height:66px;border-bottom:1px solid #eee;box-shadow:0 1px 3px rgba(0,0,0,.03)}
.brand{position:absolute;left:80px;top:22px;font-family:"Jost",sans-serif;font-weight:500;font-size:21px;color:var(--teal);display:flex;align-items:center;gap:7px}
.brand-dot{width:14px;height:14px;border-radius:50%;background:var(--teal)}
.call{position:absolute;left:457px;top:12px;display:flex;gap:8px;align-items:center;font-family:"Jost",sans-serif;color:var(--ink)}
.call small{display:block;font-size:7px}
.call strong{font-weight:400;font-size:9.5px}
.btn{display:inline-flex;align-items:center;justify-content:center;background:var(--teal);color:#fff;border-radius:11px;font-family:"Jost",sans-serif;font-size:8.5px}
.book{position:absolute;left:553px;top:12px;width:80px;height:21px;gap:5px}
.main-nav{position:absolute;top:43px;right:79px;display:flex;gap:25px;font-family:"Jost",sans-serif;font-size:8.5px;color:var(--ink)}
.main-nav .active{color:var(--teal);border-bottom:1px solid var(--teal);padding-bottom:1px}

/* hero */
.tag{position:absolute;left:78px;top:109px;background:var(--teal-soft);color:var(--teal-dark);font-family:"Jost",sans-serif;font-weight:600;font-size:6.5px;letter-spacing:.3px;padding:6px 11px;border-radius:9px}
.hero-title{position:absolute;left:78px;top:140px;font-family:"Jost",sans-serif;font-weight:700;font-size:14px;line-height:20px;letter-spacing:.4px;color:var(--ink)}
.hero-copy{position:absolute;left:79px;top:213px;width:170px;font-size:7.8px;line-height:12px;color:var(--body)}
.referral{position:absolute;left:78px;top:318px;width:118px;height:20px}
.pager{position:absolute;left:80px;top:366px;display:flex;gap:8px}
.pager span{width:16px;height:16px;border:1px solid #333;border-radius:50%;display:flex;align-items:center;justify-content:center}

/* quick links */
.quick{position:absolute;top:448px;width:267px;height:66px;background:var(--teal-soft);border-radius:0 33px 33px 0}
.quick h3{position:absolute;left:95px;top:15px;font-family:"Jost",sans-serif;font-weight:600;font-size:8.5px;letter-spacing:.4px;color:var(--teal-dark)}
.quick p{position:absolute;left:95px;top:30px;font-size:7.3px;line-height:10.5px;color:var(--ink)}
.quick .go{position:absolute;left:210px;top:16px;width:32px;height:32px;border-radius:50%;background:var(--teal);display:flex;align-items:center;justify-content:center}

/* welcome */
.divider-v{position:absolute;left:384px;width:1px;background:#555}
.welcome-kicker{position:absolute;left:408px;top:584px;font-family:"Jost",sans-serif;font-weight:500;font-size:11px;letter-spacing:.5px;color:var(--ink)}
.welcome-title{position:absolute;left:408px;top:601px;font-family:"Jost",sans-serif;font-weight:600;font-size:16.5px;letter-spacing:.6px;color:var(--teal)}
.welcome-rule{position:absolute;left:408px;top:632px;width:60px;height:2px;background:var(--teal)}
.welcome-copy{position:absolute;left:408px;top:655px;width:230px;font-size:8.4px;line-height:13.4px}
.read-more{position:absolute;left:410px;top:758px;width:70px;height:21px}

/* tiles */
.tile{position:absolute;top:864px;width:128px;height:110px;background:#fff;border-radius:6px;box-shadow:0 2px 10px rgba(0,0,0,.06);text-align:center}
.tile svg{margin-top:16px}
.tile p{margin-top:9px;font-family:"Jost",sans-serif;font-size:7.5px;letter-spacing:.4px;line-height:12px;color:var(--ink)}

/* footer */
.site-footer{position:absolute;left:0;top:1010px;width:713px;height:190px;background:var(--foot-bg);border-top:3px solid var(--teal)}
.foot-note{position:absolute;left:0;top:29px;width:713px;text-align:center;font-family:"Jost",sans-serif;font-weight:500;font-size:9.2px;line-height:14.5px;letter-spacing:.3px;color:var(--ink)}
.foot-rule{position:absolute;left:79px;width:556px;height:1px;background:var(--line)}
.foot-brand{position:absolute;left:79px;top:100px;font-family:"Jost",sans-serif;font-weight:500;font-size:19px;color:var(--teal);display:flex;align-items:center;gap:7px}
.contact{position:absolute;top:96px;display:flex;gap:7px;align-items:center;font-family:"Jost",sans-serif;font-size:7.3px;line-height:9.5px;color:var(--ink)}
.foot-nav{position:absolute;right:80px;top:127px;display:flex;gap:20px;font-family:"Jost",sans-serif;font-size:7px;color:var(--ink)}
.copyright{position:absolute;left:0;top:165px;width:713px;text-align:center;font-size:6.3px;color:#444}
</style>
</head>
<body>

<header class="site-header">
  <div class="brand"><span class="brand-dot"></span>BrightPath Care</div>
  <div class="call">
    <svg width="16" height="16" viewBox="0 0 24 24" fill="none" stroke="#333" stroke-width="1.4"><path d="M5 3h4l2 5-3 2a12 12 0 0 0 6 6l2-3 5 2v4a2 2 0 0 1-2 2A18 18 0 0 1 3 5a2 2 0 0 1 2-2z"/><path d="M14 3a7 7 0 0 1 7 7M14 7a3 3 0 0 1 3 3"/></svg>
    <div><small>Call Us:</small><strong>604.555.0142</strong></div>
  </div>
  <a class="btn book"><svg width="10" height="10" viewBox="0 0 24 24" fill="none" stroke="#fff" stroke-width="2"><rect x="3" y="5" width="18" height="16" rx="2"/><path d="M3 10h18M8 3v4M16 3v4"/></svg>Book Online</a>
  <nav class="main-nav">
    <span class="active">Home</span><span>Locations</span><span>For Patients</span><span>For Providers</span><span>About Us</span>
  </nav>
</header>

<!-- hero graphics -->
<svg class="abs" style="left:0;top:0" width="713" height="420" viewBox="0 0 713 420">
  <defs>
    <linearGradient id="heroPhoto" x1="0" y1="0" x2="1" y2="1">
      <stop offset="0" stop-color="#e9ecef"/><stop offset=".45" stop-color="#2a5fb8"/><stop offset=".7" stop-color="#d8dde2"/><stop offset="1" stop-color="#f2f2f2"/>
    </linearGradient>
  </defs>
  <rect x="400" y="134" width="226" height="226" rx="40" transform="rotate(45 513 247)" fill="#fff" stroke="#f4f4f6" stroke-width="16"/>
  <rect x="360" y="134" width="226" height="226" rx="40" transform="rotate(45 473 247)" fill="#fff" stroke="var(--faint)" stroke-width="16"/>
  <rect x="317" y="134" width="226" height="226" rx="42" transform="rotate(45 430 247)" fill="var(--frame)"/>
  <g role="img" aria-label="Photo of a clinician examining an athlete's knee on a treatment table">
    <rect x="332" y="149" width="196" height="196" rx="34" transform="rotate(45 430 247)" fill="url(#heroPhoto)"/>
  </g>
</svg>

<span class="tag">YOUR PARTNER IN HEALTH</span>
<h1 class="hero-title">SPORTS MEDICINE SERVICES<br>NOW AVAILABLE AT OUR<br>LAKESHORE LOCATION</h1>
<p class="hero-copy">BrightPath Care Clinics is continually adding and improving our services to provide patients with access to comprehensive care under one roof. Speak with your healthcare provider about how interventional MSK treatments and regenerative therapy can help you today!</p>
<a class="btn referral">Download Referral Form</a>
<div class="pager">
  <span><svg width="6" height="8" viewBox="0 0 6 8"><path d="M5 1 2 4l3 3" fill="none" stroke="#333"/></svg></span>
  <span><svg width="6" height="8" viewBox="0 0 6 8"><path d="M1 1l3 3-3 3" fill="none" stroke="#333"/></svg></span>
</div>

<!-- quick links -->
<div class="quick" style="left:80px">
  <h3>FIND A PROVIDER</h3>
  <p>The Valley's Best<br>Healthcare Providers</p>
  <span class="go"><svg width="10" height="12" viewBox="0 0 10 12"><path d="M3 2l4 4-4 4" fill="none" stroke="#fff" stroke-width="1.6"/></svg></span>
</div>
<div class="quick" style="left:368px">
  <h3>FIND PATIENTS</h3>
  <p>FIND MANY OF OUR<br>FREQUENTLY USED FORMS</p>
  <span class="go"><svg width="10" height="12" viewBox="0 0 10 12"><path d="M3 2l4 4-4 4" fill="none" stroke="#fff" stroke-width="1.6"/></svg></span>
</div>
<svg class="abs" style="left:70px;top:435px" width="600" height="90" viewBox="70 435 600 90">
  <rect x="88" y="456" width="50" height="50" rx="10" transform="rotate(45 113 481)" fill="#fff" stroke="var(--frame)" stroke-width="3"/>
  <g role="img" aria-label="Photo of a physiotherapist treating a patient's leg">
    <rect x="90" y="458" width="46" height="46" rx="9" transform="rotate(45 113 481)" fill="#cfd6de"/>
  </g>
  <rect x="376" y="456" width="50" height="50" rx="10" transform="rotate(45 401 481)" fill="#fff" stroke="var(--frame)" stroke-width="3"/>
  <g role="img" aria-label="Photo of a person stretching with a highlighted sore shoulder">
    <rect x="378" y="458" width="46" height="46" rx="9" transform="rotate(45 401 481)" fill="#b8b8bc"/>
  </g>
</svg>

<!-- welcome -->
<svg class="abs" style="left:0;top:550px" width="400" height="270" viewBox="0 550 400 270">
  <defs>
    <linearGradient id="fieldPhoto" x1="0" y1="0" x2="0" y2="1">
      <stop offset="0" stop-color="#2b63c4"/><stop offset=".55" stop-color="#3a7f3a"/><stop offset="1" stop-color="#5fb84a"/>
    </linearGradient>
  </defs>
  <rect x="120" y="580" width="210" height="210" rx="40" transform="rotate(45 225 685)" fill="#fff" stroke="#f4f4f6" stroke-width="14"/>
  <rect x="75" y="580" width="210" height="210" rx="40" transform="rotate(45 180 685)" fill="#fff" stroke="var(--faint)" stroke-width="14"/>
  <rect x="109" y="591" width="188" height="188" rx="36" transform="rotate(45 203 685)" fill="var(--frame)"/>
  <g role="img" aria-label="Photo of a medic checking a football player's knee on a grass pitch">
    <rect x="121" y="603" width="164" height="164" rx="30" transform="rotate(45 203 685)" fill="url(#fieldPhoto)"/>
  </g>
</svg>
<div class="divider-v" style="top:590px;height:82px"></div>
<span class="abs" style="left:382px;top:682px;width:5px;height:5px;border-radius:50%;background:var(--teal)"></span>
<div class="divider-v" style="top:698px;height:84px"></div>
<h2 class="welcome-kicker">WELCOME TO</h2>
<h2 class="welcome-title">BRIGHTPATH CARE CLINICS</h2>
<div class="welcome-rule"></div>
<p class="welcome-copy">At BrightPath Care Clinics, work/life balance is at the core of our culture. Our philosophy is simple: we take exceptional care of our people so that they can take exceptional care of our patients. Contact us to find out why so many healthcare providers and medical professionals have chosen to join our team.</p>
<a class="btn read-more">Read More</a>

<!-- tiles -->
<div class="tile" style="left:80px">
  <svg width="44" height="42" viewBox="0 0 44 42" fill="none" stroke="#555" stroke-width="1.1"><rect x="9" y="8" width="26" height="26" rx="5" transform="rotate(45 22 21)"/><rect x="15" y="16" width="13" height="10" rx="1"/><path d="M19 16v-2h5v2M15 20h13"/><circle cx="28" cy="26" r="3"/></svg>
  <p>SERVICES</p>
</div>
<div class="tile" style="left:223px">
  <svg width="44" height="42" viewBox="0 0 44 42" fill="none" stroke="#555" stroke-width="1.1"><rect x="9" y="8" width="26" height="26" rx="5" transform="rotate(45 22 21)"/><rect x="15" y="15" width="14" height="12" rx="1"/><path d="M15 19h14M18 13v3M26 13v3M18 22h1M21 22h1M24 22h1M18 25h1M21 25h1"/></svg>
  <p>BOOK AN<br>APPOINTMENT</p>
</div>
<div class="tile" style="left:366px">
  <svg width="44" height="42" viewBox="0 0 44 42" fill="none" stroke="#555" stroke-width="1.1"><rect x="9" y="8" width="26" height="26" rx="5" transform="rotate(45 22 21)"/><path d="M22 28s-5-5-5-9a5 5 0 0 1 10 0c0 4-5 9-5 9z"/><circle cx="22" cy="19" r="1.8"/></svg>
  <p>LOCATIONS</p>
</div>
<div class="tile" style="left:507px">
  <svg width="44" height="42" viewBox="0 0 44 42" fill="none" stroke="#555" stroke-width="1.1"><rect x="9" y="8" width="26" height="26" rx="5" transform="rotate(45 22 21)"/><path d="M17 15h3l1 3-2 1a7 7 0 0 0 4 4l1-2 3 1v3a1 1 0 0 1-1 1 11 11 0 0 1-10-10 1 1 0 0 1 1-1z"/><path d="M23 15a4 4 0 0 1 4 4"/></svg>
  <p>CONTACT US</p>
</div>

<footer class="site-footer">
  <p class="foot-note">BrightPath Care Clinics is focused on our patients first. Connect with us to<br>stay up to date with current news and upcoming events.</p>
  <div class="foot-rule" style="top:77px"></div>
  <div class="foot-brand"><span class="brand-dot"></span>BrightPath Care</div>
  <div class="contact" style="left:436px">
    <svg width="15" height="11" viewBox="0 0 15 11" fill="none" stroke="#333"><rect x=".5" y=".5" width="14" height="10"/><path d="M.5 .5 7.5 6l7-5.5M.5 10.5l5-5M14.5 10.5l-5-5"/></svg>
    <div>Email Us<br>hello@brightpathcareclinics.ca</div>
  </div>
  <div class="contact" style="left:570px">
    <svg width="14" height="14" viewBox="0 0 24 24" fill="none" stroke="#333" stroke-width="1.4"><path d="M5 3h4l2 5-3 2a12 12 0 0 0 6 6l2-3 5 2v4a2 2 0 0 1-2 2A18 18 0 0 1 3 5a2 2 0 0 1 2-2z"/><path d="M14 3a7 7 0 0 1 7 7"/></svg>
    <div>Call Us<br>604.555.0142</div>
  </div>
  <nav class="foot-nav"><span>Home</span><span>Locations</span><span>For Patients</span><span>For Providers</span><span>About Us</span></nav>
  <div class="foot-rule" style="top:145px"></div>
  <p class="copyright">Copyright © 2022 All Rights Reserved</p>
</footer>

</body>
</html>
```